Website for Excavator and Earthworks Company

We require a modern, sleek and practical website for our newly created earthworks/excavator business in Perth, Western Australia called Bluegum Ridge Earthworks.

The website should have a modern, cutting edge feel but only needs to be relatively simplistic in it's layout and eventual functionality.

Some pages it should have would be Home, About, Projects and Contact Us.

```html
<!DOCTYPE html>
<html lang="en">
<head>
<meta charset="utf-8">
<title>Bluegum Ridge Earthworks</title>
<link rel="stylesheet" href="https://fonts.googleapis.com/css2?family=Bebas+Neue&family=Krona+One&family=Inter:wght@400;500;600&display=swap">
<style>
:root{
  --lime:#c5cc2c;
  --lime-dark:#a9b01f;
  --ink:#161616;
  --dark:#262626;
  --darker:#1b1b1b;
  --orange:#d48f1b;
  --muted:#555;
  --white:#fff;
  --line:#d6d6d6;
}
*{box-sizing:border-box;margin:0;padding:0}
html,body{width:1200px;height:3979px;overflow:hidden}
body{position:relative;background:var(--white);font-family:"Inter",Arial,sans-serif;color:var(--ink)}
.abs{position:absolute}
.display{font-family:"Krona One",Arial,sans-serif;text-transform:uppercase}
.kicker{font-family:"Inter",Arial,sans-serif;font-size:14px;color:var(--lime-dark);letter-spacing:.3px;display:flex;align-items:center;gap:6px}
.kicker::before{content:"";width:30px;height:2px;background:var(--lime)}
.kicker.center::after{content:"";width:30px;height:2px;background:var(--lime)}
.btn{display:flex;align-items:center;justify-content:center;font-size:13px;font-weight:500;text-transform:uppercase;letter-spacing:.2px}
.btn-lime{background:var(--lime);color:var(--ink)}
.btn-dark{background:var(--ink);color:var(--white)}

/* header */
.brand{left:259px;top:0;width:158px;height:77px;background:var(--white);display:flex;align-items:center;justify-content:center;gap:7px}
.brand-mark{width:14px;height:14px;background:var(--lime)}
.brand-name{font-family:"Krona One",sans-serif;font-size:10px;line-height:13px;color:var(--ink);text-transform:uppercase}
.topbar{left:417px;top:0;width:523px;height:77px;background:var(--darker)}
.topbar-contact{position:absolute;left:12px;top:10px;display:flex;gap:18px;font-size:12px;color:var(--white);align-items:center}
.topbar-contact span{display:flex;align-items:center;gap:6px}
.topbar-social{position:absolute;right:12px;top:9px;display:flex;gap:5px}
.sq{width:18px;height:18px;border:1px solid #666}
.nav{position:absolute;left:30px;top:50px;display:flex;gap:38px;font-size:12.5px;color:var(--white);text-transform:uppercase}
.nav .active{color:var(--lime)}

/* hero */
.hero{left:0;top:0;width:1200px;height:710px;background:linear-gradient(180deg,#dbe8f2 0%,#c9dbe8 30%,#a9a79a 52%,#6f5b45 68%,#3e3224 100%);z-index:-1}
.hero-title{left:0;top:120px;width:1200px;text-align:center;font-family:"Bebas Neue",sans-serif;font-size:80px;line-height:64px;color:var(--ink)}
.hero-title em{font-style:normal;color:var(--lime)}
.hero-text{left:300px;top:262px;width:600px;text-align:center;font-size:14px;line-height:21px;color:var(--ink)}
.scroll{left:553px;top:664px;width:92px;height:92px;border-radius:50%;background:var(--white);border:2px solid var(--lime);display:flex;align-items:center;justify-content:center}

/* about */
.about-dark{left:0;top:832px;width:402px;height:485px;background:linear-gradient(135deg,#3a3128,#1c1a17)}
.about-photo{left:140px;top:875px;width:459px;height:400px;background:linear-gradient(180deg,#b7cbe0 0%,#d6dde4 45%,#8a6a49 75%,#5a4330 100%)}
.about-title{left:659px;top:903px;font-size:32px;line-height:38px;color:var(--ink)}
.about-sub{left:659px;top:988px;font-size:15px;color:var(--lime-dark)}
.about-text{left:659px;top:1024px;width:380px;font-size:12px;line-height:23px;color:#333}

/* services */
.svc-intro{left:0;top:1411px;width:412px;height:599px;background:linear-gradient(160deg,#4a4a48,#1f1f1e 70%)}
.svc-intro .display{position:absolute;left:99px;top:180px;font-size:32px;line-height:40px;color:var(--white)}
.svc-intro p{position:absolute;left:99px;top:275px;width:260px;font-size:15px;line-height:28px;color:var(--white)}
.svc{width:263px;height:300px;padding:62px 30px 0 35px;color:var(--white)}
.svc.orange{background:var(--orange)}
.svc.dark{background:var(--dark)}
.svc svg{display:block;margin-bottom:12px}
.svc h3{font-family:"Krona One",sans-serif;font-weight:400;font-size:16px;line-height:20px;margin-bottom:10px}
.svc p{font-size:12px;line-height:19px}

/* projects */
.proj{overflow:hidden;color:var(--white)}
.proj .cap{position:absolute;left:12px;right:18px;bottom:14px}
.proj h4{font-family:"Krona One",sans-serif;font-weight:400;font-size:14px;margin-bottom:6px}
.proj p{font-size:11.5px;line-height:16px}

/* quote */
.quote{left:0;top:2705px;width:1200px;height:666px;background:linear-gradient(180deg,#2a2a28,#3a3630 60%,#24221f)}
.quote-title{left:0;top:2835px;width:1200px;text-align:center;font-size:34px;color:var(--white)}
.quote-text{left:380px;top:2878px;width:440px;text-align:center;font-size:14px;line-height:22px;color:var(--white)}
.form{left:210px;top:2941px;width:491px;height:317px;background:var(--white)}
.field{position:absolute;font-size:12px;color:#222;border-bottom:1px solid var(--line);padding-bottom:24px;height:50px}
.info{left:701px;top:2941px;width:289px;height:317px;background:var(--lime);padding:36px 46px}
.info h3{font-family:"Krona One",sans-serif;font-weight:400;font-size:15px;line-height:22px;margin-bottom:16px}
.info-row{display:flex;gap:12px;font-size:12px;line-height:18px;margin-bottom:14px}
.info-row svg{flex:none}
.info-social{display:flex;gap:8px;margin-top:22px}
.info-social .sq{width:28px;height:28px;border:1.5px solid var(--ink)}

/* newsletter */
.news-title{left:0;top:3460px;width:1200px;text-align:center;font-size:18px;color:#1e3a7a}
.news-text{left:0;top:3498px;width:1200px;text-align:center;font-size:14px;line-height:21px;color:#222}
.news-input{left:357px;top:3556px;width:332px;height:38px;border:1px solid var(--line);font-size:12px;padding:11px 12px;color:#333}
.news-btn{left:689px;top:3556px;width:153px;height:38px;background:var(--lime);font-family:"Krona One",sans-serif;font-size:15px}

/* footer */
.footer-nav{left:352px;top:3790px;display:flex;gap:38px;font-size:13px;text-transform:uppercase}
.footer-nav .active{color:var(--lime-dark)}
.footer-band{left:141px;top:3824px;width:918px;height:90px;background:var(--lime);display:flex;justify-content:center;gap:62px;padding-top:30px;font-size:12.5px;line-height:18px}
.footer-band div{display:flex;gap:12px}
.copy{left:141px;top:3938px;font-size:12px}
.foot-social{left:925px;top:3930px;display:flex;gap:8px}
.foot-social .sq{width:28px;height:28px;border:1.5px solid var(--ink)}
</style>
</head>
<body>

<!-- header -->
<div class="hero abs" role="img" aria-label="Site engineer with clipboard overlooking an open earthworks site with excavators and a loader"></div>
<div class="brand abs"><span class="brand-mark"></span><span class="brand-name">Bluegum Ridge<br>Earthworks</span></div>
<div class="topbar abs">
  <div class="topbar-contact">
    <span><svg width="12" height="12" viewBox="0 0 24 24"><path d="M6 2l4 4-2 3c1 3 4 6 7 7l3-2 4 4-3 4C10 22 2 14 2 5z" fill="var(--lime)"/></svg>Call Us: (123) 456 7890</span>
    <span><svg width="16" height="12" viewBox="0 0 16 12"><rect width="16" height="12" fill="var(--lime)"/><path d="M0 0l8 7 8-7" stroke="#1b1b1b" fill="none"/></svg>Email Us: info@bluegumridge.example</span>
  </div>
  <div class="topbar-social"><span class="sq"></span><span class="sq" style="background:var(--lime);border-color:var(--lime)"></span><span class="sq"></span><span class="sq"></span></div>
  <nav class="nav"><span class="active">Home</span><span>About Us</span><span>Services</span><span>Projects</span><span>Contact Us</span></nav>
</div>

<!-- hero -->
<h1 class="hero-title abs" style="font-weight:400">Earth Moved<br>With <em>Precision</em></h1>
<p class="hero-text abs">Professional excavation, bulk earthworks, site preparation and land development services across Perth and Western Australia.</p>
<div class="btn btn-lime abs" style="left:432px;top:327px;width:162px;height:37px">Get A Quote Today</div>
<div class="btn btn-dark abs" style="left:603px;top:327px;width:164px;height:37px">View Our Projects</div>
<div class="scroll abs"><svg width="24" height="40" viewBox="0 0 24 40"><rect x="5" y="2" width="14" height="22" rx="7" fill="none" stroke="#222" stroke-width="1.5"/><line x1="12" y1="7" x2="12" y2="12" stroke="#222" stroke-width="1.5"/><path d="M7 28l5 4 5-4M7 33l5 4 5-4" fill="none" stroke="#222" stroke-width="1.5"/></svg></div>

<!-- about -->
<div class="about-dark abs" role="img" aria-label="Dark close-up of an excavator bucket in soil"></div>
<div class="about-photo abs" role="img" aria-label="Yellow tracked excavator standing on a mound of earth"></div>
<div class="kicker abs" style="left:659px;top:872px">ABOUT</div>
<h2 class="about-title display abs" style="font-weight:400">Bluegum Ridge<br>Earthworks</h2>
<p class="about-sub abs">Bluegum Ridge Earthworks: Building Perth's Future</p>
<div class="about-text abs">
  <p>Based in Perth, Western Australia, Bluegum Ridge Earthworks is a premier excavation and earthworks company specializing in residential, commercial, and industrial projects.</p>
  <p>With over 15 years of industry experience, our team combines cutting-edge equipment with skilled operators to deliver exceptional results on time and within budget.</p>
  <p>We pride ourselves on our commitment to safety, precision, and environmental responsibility in every project we undertake.</p>
</div>
<div class="btn btn-lime abs" style="left:659px;top:1237px;width:164px;height:37px">Contact Our Team</div>

<!-- services -->
<div class="svc-intro abs" role="img" aria-label="Excavator on a dark cloudy work site">
  <div class="kicker" style="position:absolute;left:99px;top:160px;color:var(--lime)">WHAT WE DO</div>
  <h2 class="display" style="font-weight:400">Our<br>Services</h2>
  <p>Comprehensive earthmoving and excavation solutions for projects of all sizes across Perth and regional WA.</p>
</div>
<div class="abs" style="left:412px;top:1411px;display:grid;grid-template-columns:263px 262px 263px;grid-template-rows:300px 299px">
  <div class="svc orange"><svg width="52" height="50" viewBox="0 0 52 50" fill="none" stroke="#fff" stroke-width="3"><rect x="4" y="30" width="28" height="12" rx="6"/><rect x="8" y="18" width="14" height="12"/><path d="M22 22l14-14 10 10"/><path d="M46 18v8h-6"/></svg><h3>Bulk<br>Earthworks</h3><p>Large-scale cut and fill operations, land levelling, and soil compaction for subdivisions and commercial developments.</p></div>
  <div class="svc dark"><svg width="52" height="50" viewBox="0 0 52 50" fill="none" stroke="#fff" stroke-width="3"><path d="M4 46h44"/><path d="M10 46V20h14v26"/><circle cx="34" cy="14" r="8"/><path d="M28 46l10-16"/></svg><h3>Land<br>Clearing</h3><p>Vegetation removal, stump grinding, and site preparation for residential, agricultural and commercial properties.</p></div>
  <div class="svc orange"><svg width="52" height="50" viewBox="0 0 52 50" fill="none" stroke="#fff" stroke-width="3"><path d="M10 46L20 4h6l10 42"/><path d="M14 30h18M16 20h14"/><path d="M36 46h12"/></svg><h3>Road &amp; Driveway Construction</h3><p>Formation, grading and compaction for access roads, farm tracks, and residential driveways.</p></div>
  <div class="svc dark"><svg width="52" height="50" viewBox="0 0 52 50" fill="none" stroke="#fff" stroke-width="3"><path d="M6 4h20l10 10v32H6z"/><path d="M16 24c6 0 6 10 12 10s6-10 12-10" /><path d="M16 36c6 0 6 8 12 8"/></svg><h3>Dam<br>&amp; Drainage</h3><p>Dam construction, excavation, lining, and drainage solutions for flood mitigation and water management.</p></div>
  <div class="svc orange"><svg width="52" height="50" viewBox="0 0 52 50" fill="none" stroke="#fff" stroke-width="3"><path d="M14 46V4h6v42"/><path d="M4 10h40M34 10v14"/><rect x="28" y="30" width="16" height="16"/></svg><h3>Site<br>Preparation</h3><p>Complete site preparation for residential and commercial construction, including slab foundations and pad preparation.</p></div>
  <div class="svc dark"><svg width="52" height="50" viewBox="0 0 52 50" fill="none" stroke="#fff" stroke-width="3"><path d="M4 22h30v14H4z"/><circle cx="12" cy="40" r="4"/><circle cx="28" cy="40" r="4"/><circle cx="40" cy="14" r="8"/><path d="M10 22l6-10h10"/></svg><h3>Material<br>Supply &amp; Removal</h3><p>Supply of quality fill material, sand, gravel, and removal of excess spoil from your site.</p></div>
</div>

<!-- projects -->
<div class="kicker center abs" style="left:520px;top:2101px">CREATIONS</div>
<h2 class="display abs" style="left:0;top:2133px;width:1200px;text-align:center;font-size:30px;font-weight:400">Our Projects</h2>
<div class="proj abs" style="left:141px;top:2205px;width:325px;height:156px;background:linear-gradient(180deg,#8a8f8e,#5e5a4c 60%,#2b2d2a)" role="img" aria-label="Excavator beside a house on a misty autumn hillside">
  <div class="cap"><h4>Lorem ipsum dolor sit amet,</h4><p>Duis autem vel eum iriure dolor in hendrerit in vulputate velit esse molestie consequat.</p></div></div>
<div class="proj abs" style="left:477px;top:2205px;width:286px;height:228px;background:linear-gradient(180deg,#b08a55,#8a6a45 55%,#3b3226)" role="img" aria-label="Aerial view of an excavator digging in rocky ground">
  <div class="cap" style="left:21px"><h4>Lorem ipsum dolorsit</h4><p>Duis autem vel eum iriure dolor in hendrerit in vulputate velit esse mole.</p></div></div>
<div class="proj abs" style="left:772px;top:2205px;width:287px;height:228px;background:linear-gradient(180deg,#6f7a55,#5a5a3e 55%,#2c2c22)" role="img" aria-label="Excavator working among trees at a clearing site">
  <div class="cap" style="left:18px"><h4>Lorem ipsum dolor amet</h4><p>Duis autem vel eum iriure dolor in hendrerit in vulputate velit esse mole.</p></div></div>
<div class="proj abs" style="left:141px;top:2373px;width:325px;height:239px;background:linear-gradient(180deg,#c9c4b4,#8a7a60 45%,#2e2820)" role="img" aria-label="Excavator silhouetted against a sunset">
  <div class="cap"><h4>Lorem ipsum dolor sit amet,</h4><p>Duis autem vel eum iriure dolor in hendrerit in vulputate velit esse molestie consequat.</p></div></div>
<div class="proj abs" style="left:477px;top:2444px;width:582px;height:168px;background:linear-gradient(90deg,#7d8f5a,#9a9a88 40%,#4a4f45 70%,#2d302c)" role="img" aria-label="Aerial view of a suburban street under construction with machinery">
  <div class="cap" style="left:395px;top:18px;bottom:auto"><h4>Lorem ipsum<br>dolor sit amet,</h4><p>Duis autem vel eum iriure dolor in hendrerit in vulputate velit esse molestie consequat.</p></div></div>

<!-- quote -->
<div class="quote abs" role="img" aria-label="Dim construction site with excavators and buildings"></div>
<div class="kicker center abs" style="left:504px;top:2797px;color:var(--lime)">QUICK INQUIRY</div>
<h2 class="quote-title display abs" style="font-weight:400">Request A Quote</h2>
<p class="quote-text abs">Ready to move earth? Contact our Perth team for a no-obligation site assessment and quote.</p>
<div class="form abs">
  <div class="field" style="left:26px;top:36px;width:204px">First name*</div>
  <div class="field" style="left:257px;top:36px;width:204px">Last name*</div>
  <div class="field" style="left:26px;top:92px;width:204px">Your phone*</div>
  <div class="field" style="left:257px;top:92px;width:204px">Your email*</div>
  <div class="field" style="left:26px;top:148px;width:435px;height:96px">Message</div>
  <div class="btn btn-lime abs" style="left:327px;top:250px;width:166px;height:37px;font-weight:600;font-size:14px">Submit Now</div>
</div>
<div class="info abs">
  <h3>Contact<br>Information</h3>
  <div class="info-row"><svg width="24" height="26" viewBox="0 0 24 26"><path d="M12 1a8 8 0 018 8c0 6-8 13-8 13S4 15 4 9a8 8 0 018-8z" fill="#161616"/><circle cx="12" cy="9" r="3" fill="var(--lime)"/><path d="M4 24h16" stroke="#161616" stroke-width="2"/></svg><span>123, Building Name, Street<br>City, State XY 123456</span></div>
  <div class="info-row"><svg width="24" height="24" viewBox="0 0 24 24"><path d="M6 3l4 4-2 3c1 3 4 6 7 7l3-2 4 4-3 4C10 23 1 14 2 6z" fill="none" stroke="#161616" stroke-width="2"/></svg><span>PHONE<br>(123) 456 7890</span></div>
  <div class="info-row"><svg width="24" height="20" viewBox="0 0 24 20"><rect x="1" y="2" width="22" height="16" fill="#161616"/><path d="M1 2l11 9 11-9" stroke="var(--lime)" stroke-width="1.5" fill="none"/></svg><span>EMAIL<br>info@bluegumridge.example</span></div>
  <div class="info-social"><span class="sq"></span><span class="sq"></span><span class="sq"></span><span class="sq"></span></div>
</div>

<!-- newsletter -->
<h2 class="news-title display abs" style="font-weight:400">Subscribe To Our Newsletter</h2>
<p class="news-text abs">Want to keep up to date with all our latest news and information?<br>Enter your email below to be added to our mailing list.</p>
<div class="news-input abs">Enter your email address</div>
<div class="news-btn btn abs">Subscribe</div>

<!-- footer -->
<div class="abs" style="left:141px;top:3644px;width:918px;height:1px;background:var(--line)"></div>
<div class="abs" style="left:0;top:3700px;width:1188px;display:flex;justify-content:center;align-items:center;gap:10px">
  <span class="brand-mark" style="width:20px;height:20px"></span>
  <span class="brand-name" style="font-size:16px;line-height:21px">Bluegum Ridge<br>Earthworks</span>
</div>
<div class="abs" style="left:849px;top:3659px;width:232px;height:170px;background:radial-gradient(ellipse at 55% 60%,#e39a3a 0%,#c07a2a 35%,rgba(255,255,255,0) 70%)" role="img" aria-label="Orange excavator"></div>
<nav class="footer-nav abs"><span class="active">Home</span><span>About Us</span><span>Services</span><span>Projects</span><span>Contact Us</span></nav>
<div class="footer-band abs">
  <div><svg width="26" height="30" viewBox="0 0 24 26"><path d="M12 1a8 8 0 018 8c0 6-8 13-8 13S4 15 4 9a8 8 0 018-8z" fill="#161616"/><circle cx="12" cy="9" r="3" fill="var(--lime)"/><path d="M4 24h16" stroke="#161616" stroke-width="2"/></svg><span>123, Building Name, Street<br>City, State XY 123456</span></div>
  <div><svg width="26" height="26" viewBox="0 0 24 24"><path d="M6 3l4 4-2 3c1 3 4 6 7 7l3-2 4 4-3 4C10 23 1 14 2 6z" fill="none" stroke="#161616" stroke-width="2"/></svg><span>PHONE<br>(123) 456 7890</span></div>
  <div><svg width="26" height="20" viewBox="0 0 24 20"><rect x="1" y="2" width="22" height="16" fill="#161616"/><path d="M1 2l11 9 11-9" stroke="var(--lime)" stroke-width="1.5" fill="none"/></svg><span>EMAIL<br>info@bluegumridge.example</span></div>
</div>
<p class="copy abs">© 2026 Bluegum Ridge Earthworks. All Rights Reserved.</p>
<div class="foot-social abs"><span class="sq"></span><span class="sq"></span><span class="sq"></span><span class="sq"></span></div>

</body>
</html>
```